Meadow Paw Web Site

We have basically a start up business that I need help with. This project is just for the web site.

Our product is a frozen raw pet food that promotes weight control, less shedding, smaller stools and an overall better health. The product is in nugget form similar to what you would see in a steak shish kabob. I only share that with you in case you want to incorporate that in the design.

We have been in business for 17 years but all of our sales have been word of mouth. We are going to be launching an infomercial this summer and I need everything stated previously to be completed before we can launch the infomercial.

We need the following (6) pages:

Home:
This is where we need to have the ability to purchase our products. Our main goal is to get the consumer to purchase our product. We have our own shopping cart so we just need to allow for the insertion of that shopping cart.

Why Raw:
This will just be a page with 4-5 paragraphs and an embedded YouTube video.

How to Use:
We will need a page with a chart (4 Columns wide with 6 rows) as well as an embedded YouTube video.

Customer Success Stories:
Allow us to add these as we move forward. I need a placeholder for an image of the customers pet and a paragraph or two explaining the situation

Where to Buy:
- Online - Find a Retailer - Find a Local Distributor - Call to Order

Contact Us:
Copper Ridge Holdings, Inc.
2740 Copper Rd
Eagan, MN 55148
(800) xxx-xxxx

We need to provide links to our to be created... Facebook page, Twitter Account, Youtube Channel, Google circle, Blog
Updates

All, I have received many front page designs that look good.  Please notice in the brief that I need multiple pages built not just the home page.  

Thanks,

Dale

Reason: I need to see the rest of the pages. Thanks, Dale

Target Market(s)

Women between the ages of 30 & 60.

Industry/Entity Type

Shopping

```html
<!DOCTYPE html>
<html lang="en">
<head>
<meta charset="utf-8">
<title>Meadow Paw – Where to Buy</title>
<link rel="stylesheet" href="https://fonts.googleapis.com/css2?family=Oswald:wght@300;400;500&family=Open+Sans:wght@400;600&display=swap">
<style>
:root{
  --orange:#d2560a;
  --orange-light:#f07f1c;
  --orange-dark:#b8470a;
  --rust:#c84a0c;
  --olive:#2e3410;
  --header-top:#e8e6e3;
  --header-bottom:#d9d7d4;
  --page-top:#fbeeee;
  --page-bottom:#fdfafa;
  --panel-pink:#f6d9da;
  --panel-pink-dark:#e6b3b6;
  --field:#fdeeee;
  --footer:#2c2c2e;
  --footer-bottom:#1d1d1f;
  --footer-head:#f0f0f0;
  --footer-text:#b2b2b2;
  --divider:#4c4c50;
  --yellow:#f7d41c;
}
*{box-sizing:border-box;margin:0;padding:0}
html,body{width:1200px;height:1063px;overflow:hidden}
body{position:relative;font-family:"Open Sans",Verdana,sans-serif;background:linear-gradient(var(--page-top),var(--page-bottom) 600px);}
a{text-decoration:none;color:inherit}

.site-header{position:absolute;left:0;top:0;width:1200px;height:195px;background:linear-gradient(135deg,var(--header-top),var(--header-bottom));}
.brand{position:absolute;left:120px;top:36px;display:flex;align-items:center;gap:12px}
.brand-mark{width:40px;height:40px;background:var(--orange)}
.brand-name{font-family:"Oswald",sans-serif;font-weight:500;font-size:34px;color:var(--orange)}

.account-links{position:absolute;right:123px;top:25px;font-family:"Oswald",sans-serif;font-size:12px;color:var(--rust);letter-spacing:.2px}
.account-links span{margin:0 5px}
.auth{position:absolute;right:120px;top:64px;display:flex;gap:8px}
.btn-pill{height:25px;border-radius:13px;font-size:13px;display:flex;align-items:center;justify-content:center;box-shadow:0 1px 2px rgba(0,0,0,.3)}
.btn-signin{width:84px;background:linear-gradient(var(--orange-light),var(--orange-dark));color:#fff}
.btn-register{width:84px;background:linear-gradient(#fde873,var(--yellow));color:#3a2a00}

.cart{position:absolute;left:623px;top:118px;display:flex;align-items:center;font-family:"Oswald",sans-serif;font-size:15px;color:var(--rust)}
.cart svg{margin-right:12px}
.cart-count{margin-left:34px}
.site-search{position:absolute;left:865px;top:117px;width:215px;height:32px;border-radius:16px;background:#fff;border:1px solid #ddd;font-size:13px;color:var(--rust);padding:8px 0 0 19px}
.site-search svg{position:absolute;right:14px;top:8px}

.main-nav{position:absolute;left:120px;top:172px;width:960px;height:47px;border-radius:5px;background:linear-gradient(var(--orange-light),var(--orange) 60%,var(--orange-dark));display:flex;box-shadow:0 1px 3px rgba(0,0,0,.25)}
.main-nav a{display:flex;align-items:center;justify-content:center;font-family:"Oswald",sans-serif;font-size:19px;color:#fff;border-right:1px solid rgba(120,40,0,.35);box-shadow:1px 0 0 rgba(255,170,90,.35)}
.main-nav a:last-child{border:0;box-shadow:none}

.page-title{position:absolute;left:120px;top:252px;font-family:"Oswald",sans-serif;font-size:27px;font-weight:400;color:var(--olive);letter-spacing:-.3px}
.page-title em{font-style:normal;color:var(--rust)}
.title-rule{position:absolute;left:120px;top:288px;width:956px;border-top:2px dotted #b9a9a6}

.finder{position:absolute;top:327px;width:458px;height:56px;background:linear-gradient(var(--panel-pink),var(--panel-pink-dark));box-shadow:0 2px 3px rgba(0,0,0,.15)}
.finder-field{position:absolute;left:13px;top:12px;width:335px;height:34px;border-radius:4px;background:var(--field);box-shadow:inset 0 1px 2px rgba(0,0,0,.15);font-family:"Oswald",sans-serif;font-weight:300;font-size:16px;color:#555;padding:5px 0 0 33px}
.finder-field svg{position:absolute;left:8px;top:9px}
.finder-btn{position:absolute;left:368px;top:13px;width:76px;height:31px;border-radius:3px;background:linear-gradient(var(--orange-light),var(--orange-dark));font-family:"Oswald",sans-serif;font-size:14px;color:#fff;display:flex;align-items:center;justify-content:center;border:1px solid #a13d06}

.promo{position:absolute;top:414px;width:460px;height:251px;overflow:hidden;box-shadow:0 2px 3px rgba(0,0,0,.15)}
.photo-shop{position:absolute;inset:0;background:linear-gradient(120deg,#3e4a68,#6b5a44 45%,#2c3f8a 80%,#4a3a2a)}
.promo-label{position:absolute;right:0;top:166px;width:281px;height:54px;background:rgba(196,74,12,.92);font-family:"Oswald",sans-serif;font-size:29px;color:#fff;display:flex;align-items:center;justify-content:center}
.promo-call{background:#fff}
.photo-agent{position:absolute;right:0;top:0;width:190px;height:251px;background:linear-gradient(90deg,#fff,#ead6c9 40%,#caa58f)}
.call-head{position:absolute;left:26px;top:30px;font-family:"Oswald",sans-serif;font-size:33px;color:var(--rust)}
.call-phone{position:absolute;left:27px;top:74px;font-family:"Open Sans",sans-serif;font-size:24px;color:#444}
.pattern-area{position:absolute;left:0;top:120px;width:240px;height:131px;background:linear-gradient(100deg,#e6f4f5,#cdebe6 50%,#f4f0cf)}

.site-footer{position:absolute;left:0;top:745px;width:1200px;height:275px;background:var(--footer)}
.foot-col{position:absolute;top:33px;height:200px}
.foot-col h3{font-family:"Oswald",sans-serif;font-weight:400;font-size:20px;color:var(--footer-head);margin-bottom:13px}
.foot-col li{list-style:none;font-size:12.5px;color:var(--footer-text);line-height:24px}
.foot-divider{position:absolute;top:40px;height:190px;border-left:1px dotted var(--divider)}
.contact-sub{font-size:13px;color:var(--footer-text);margin-bottom:3px}
.contact-note{font-size:11px;color:var(--footer-text);line-height:20px;width:190px}
.contact-phone{display:flex;align-items:center;gap:6px;margin-top:7px;font-family:Georgia,serif;font-size:14px;color:var(--footer-text)}
.news-note{font-size:12.5px;color:var(--footer-text);line-height:16px;width:220px}
.news-field{margin-top:12px;width:237px;height:32px;background:#fff;border-radius:2px;font-size:14px;color:#aaa;padding:6px 12px}
.news-btn{position:absolute;left:152px;top:157px;width:86px;height:28px;background:var(--rust);color:#fff;font-size:14px;display:flex;align-items:center;justify-content:center}
.social{position:absolute;left:74px;top:200px;display:flex;gap:9px}
.social span{width:26px;height:26px;border-radius:3px}

.bottom-bar{position:absolute;left:0;top:1020px;width:1200px;height:43px;background:var(--footer-bottom);font-size:12px;color:#8a8a8a;padding:15px 0 0 121px}
</style>
</head>
<body>

<header class="site-header">
  <div class="brand"><span class="brand-mark"></span><span class="brand-name">Meadow Paw</span></div>
  <nav class="account-links">MY ACCOUNT<span>/</span>WISH LIST<span>/</span>MY CART<span>/</span>CHECKOUT</nav>
  <div class="auth"><a class="btn-pill btn-signin">Sing in</a><a class="btn-pill btn-register">Register</a></div>
  <div class="cart">
    <svg width="28" height="22" viewBox="0 0 28 22"><path d="M2 8h24l-3 12H5z" fill="#e07a22"/><path d="M8 8l5-7M20 8l-5-7" stroke="#e07a22" stroke-width="2" fill="none"/><path d="M9 11v6M14 11v6M19 11v6" stroke="#fff" stroke-width="1.5"/></svg>
    SHOPPING CART<span class="cart-count">(2) ITEMS</span>
  </div>
  <div class="site-search">Search.......
    <svg width="16" height="16" viewBox="0 0 16 16"><circle cx="6.5" cy="6.5" r="4.8" stroke="var(--rust)" stroke-width="2.2" fill="none"/><path d="M10 10l4.5 4.5" stroke="var(--rust)" stroke-width="2.6"/></svg>
  </div>
</header>

<nav class="main-nav">
  <a style="width:78px"><svg width="22" height="18" viewBox="0 0 22 18"><path d="M11 1L1 10h3v7h5v-5h4v5h5v-7h3z" fill="#fff"/></svg></a>
  <a style="width:145px">Why Raw</a>
  <a style="width:172px">How to Use</a>
  <a style="width:191px">Where to Buy</a>
  <a style="width:214px">Success Stories</a>
  <a style="width:160px">Contact Us</a>
</nav>

<h1 class="page-title">WHERE <em>TO BUY</em></h1>
<div class="title-rule"></div>

<div class="finder" style="left:120px">
  <div class="finder-field"><svg width="17" height="17" viewBox="0 0 17 17"><circle cx="7" cy="7" r="5" stroke="#777" stroke-width="1.8" fill="none"/><path d="M10.5 10.5l5 5" stroke="#777" stroke-width="2"/></svg>Search here for retailer</div>
  <a class="finder-btn">SEARCH</a>
</div>
<div class="finder" style="left:620px">
  <div class="finder-field"><svg width="17" height="17" viewBox="0 0 17 17"><circle cx="7" cy="7" r="5" stroke="#777" stroke-width="1.8" fill="none"/><path d="M10.5 10.5l5 5" stroke="#777" stroke-width="2"/></svg>Search here for local distributor</div>
  <a class="finder-btn">SEARCH</a>
</div>

<section class="promo" style="left:120px">
  <div class="photo-shop" role="img" aria-label="Small dog sitting in a shopping cart full of groceries"></div>
  <div class="promo-label">ONLINE SHOPPING CART</div>
</section>
<section class="promo promo-call" style="left:620px">
  <div class="pattern-area" role="img" aria-label="Decorative band of coloured tiles"></div>
  <div class="photo-agent" role="img" aria-label="Customer service agent wearing a headset"></div>
  <div class="call-head">CALL TO ORDER TODAY !</div>
  <div class="call-phone">0-000-000-0000</div>
</section>

<footer class="site-footer">
  <div class="foot-col" style="left:120px"><h3>Quick Links</h3><ul><li>Why Raw</li><li>How to Use</li><li>Where to Buy</li><li>Success Stories</li><li>How to Use</li><li>Where to Buy</li><li>Contact Us</li></ul></div>
  <div class="foot-divider" style="left:244px"></div>
  <div class="foot-col" style="left:273px"><h3>Top Products</h3><ul><li>Product 1</li><li>Product 2</li><li>Product 3</li><li>Product 4</li><li>Product 5</li><li>Product 6</li><li>Product 7</li></ul></div>
  <div class="foot-divider" style="left:399px"></div>
  <div class="foot-col" style="left:428px"><h3>Where to Buy</h3><ul><li>Find a Retailer</li><li>Find a Local Distributor</li><li>Call to Order</li></ul></div>
  <div class="foot-divider" style="left:583px"></div>
  <div class="foot-col" style="left:616px"><h3>Contact Information</h3>
    <p class="contact-sub">PUBLISHING PACKAGES</p>
    <p class="contact-note">Lorem Ipsum is therefore always free from repetition</p>
    <p class="contact-phone"><svg width="18" height="20" viewBox="0 0 18 20"><path d="M4 1l4 4-2 3c1 3 3 5 5 6l3-2 4 4-3 3C8 18 1 10 1 4z" fill="#d8d8d8"/></svg>+0 (000) 000-0000</p>
  </div>
  <div class="foot-divider" style="left:815px"></div>
  <div class="foot-col" style="left:842px;width:240px"><h3>Newsletter</h3>
    <p class="news-note">combined with a handful of model sentence structures.</p>
    <div class="news-field">Email address</div>
    <a class="news-btn">Subscribe</a>
    <div class="social">
      <span style="background:#3b64c4"></span><span style="background:#37506d"></span><span style="background:#f28a12"></span><span style="background:#d4363a"></span><span style="background:#b3282a"></span>
    </div>
  </div>
</footer>

<div class="bottom-bar">Company Name © 2014. Privacy Policy</div>

</body>
</html>
```